Flight school sign for building, banner, and bilboard

This sign is primarily for use on the side of our flight school building to draw attention for current and future flight school students. We offer airplane and helicopter flight training, ground school training and seminars, airplane and helicopter rentals, multi-engine training, and more. I would like a professional but exciting sign that can be used across a multitude of signage options such as banners, banner ads, billboard, and other mediums so that our sign is consistent and recognizable.

Contact Information for Business Card

The business card should match our company sign somewhat but not exactly. We want good and exciting imagery or wording and energizing/exciting colors.

```html
<!DOCTYPE html>
<html lang="en">
<head>
<meta charset="utf-8">
<title>Vega Aviation – Flight School Banner</title>
<link rel="stylesheet" href="https://fonts.googleapis.com/css2?family=Michroma&family=Oswald:wght@500&display=swap">
<style>
  :root {
    --page: #e4e4e4;
    --navy-deep: #020b33;
    --navy: #0b1c5e;
    --red: #e92535;
    --white: #ffffff;
    --silver: #d9dce4;
    --sky-warm: #e9b76a;
    --sky-cloud: #6f6a70;
  }
  * { box-sizing: border-box; margin: 0; padding: 0; }
  html, body { width: 1200px; height: 1200px; overflow: hidden; }
  body { background: var(--page); position: relative; font-family: "Michroma", sans-serif; }

  .banner {
    position: absolute; left: 35px; top: 363px;
    width: 1129px; height: 474px;
    background: var(--navy-deep);
    overflow: hidden;
  }
  .banner-art { position: absolute; inset: 0; width: 1129px; height: 406px; }

  .brand-mark {
    position: absolute; left: 221px; top: 18px;
    width: 90px; height: 90px; border-radius: 50%;
    background: var(--red);
  }
  .brand-name {
    position: absolute; left: 70px; top: 132px; width: 392px;
    text-align: center;
    font-size: 30px; color: var(--white); letter-spacing: 0.5px;
    white-space: nowrap;
  }

  .services { position: absolute; left: 52px; top: 204px; list-style: none; }
  .services li {
    position: relative; padding-left: 18px; margin-bottom: 12px;
    font-size: 15.5px; line-height: 19px; letter-spacing: 2.4px;
    color: var(--silver); text-transform: uppercase;
  }
  .services li::before {
    content: ""; position: absolute; left: 1px; top: 4px;
    width: 8px; height: 8px;
    border-top: 3px solid var(--red); border-right: 3px solid var(--red);
    transform: rotate(45deg);
  }

  .contact-bar {
    position: absolute; left: 0; bottom: 0; width: 100%; height: 68px;
    background: var(--red);
    font-family: "Oswald", sans-serif; font-weight: 500;
    color: var(--white); font-size: 35px; line-height: 68px;
  }
  .contact-item { position: absolute; top: 0; display: flex; align-items: center; gap: 10px; height: 68px; }
  .contact-item svg { width: 30px; height: 30px; fill: var(--navy); flex: none; }
  .contact-web { left: 32px; }
  .contact-phone { left: 410px; }
  .contact-mail { left: 670px; }
</style>
</head>
<body>
  <section class="banner">
    <svg class="banner-art" viewBox="0 0 1129 406" aria-hidden="false">
      <defs>
        <linearGradient id="leftPhoto" x1="0" y1="0" x2="1" y2="1">
          <stop offset="0" stop-color="#0a1650"/>
          <stop offset="0.6" stop-color="#1a2d6e"/>
          <stop offset="1" stop-color="#071040"/>
        </linearGradient>
        <linearGradient id="sky" x1="0" y1="0" x2="0.3" y2="1">
          <stop offset="0" stop-color="#7b7578"/>
          <stop offset="0.45" stop-color="#c99a63"/>
          <stop offset="0.7" stop-color="#f0c27a"/>
          <stop offset="1" stop-color="#3a4250"/>
        </linearGradient>
      </defs>
      <rect x="0" y="0" width="1129" height="406" fill="var(--navy-deep)"/>
      <rect x="0" y="90" width="500" height="316" fill="url(#leftPhoto)" opacity="0.6"
            role="img" aria-label="Faded photo of a twin-engine airplane parked on the ramp"/>
      <path d="M600 406 L1129 406 L1129 330 C1000 320 860 350 700 340 C640 335 600 360 600 406 Z" fill="var(--navy)"/>
      <path class="wave" d="M494 250 C520 330 610 370 720 372 C860 374 1000 330 1129 350 L1129 336 C1000 318 860 360 720 358 C620 356 540 320 500 240 Z" fill="var(--white)"/>
      <path d="M600 0 L1129 0 L1129 322 C1000 300 860 345 720 343 C620 342 545 310 512 260 C480 180 510 60 570 0 Z"
            fill="url(#sky)" role="img"
            aria-label="Photo of a high-wing single-engine airplane flying over a coastal city at sunset"/>
    </svg>

    <div class="brand-mark" aria-hidden="true"></div>
    <h1 class="brand-name">VEGA AVIATION</h1>

    <ul class="services">
      <li>Airplane and helicopter<br>flight training</li>
      <li>Ground school training<br>and seminars</li>
      <li>Airplane and helicopter<br>rentals</li>
      <li>Multi-engine training</li>
    </ul>

    <footer class="contact-bar">
      <div class="contact-item contact-web">
        <svg viewBox="0 0 24 24" aria-hidden="true"><path d="M12 1a11 11 0 1 0 0 22 11 11 0 0 0 0-22zm0 2c1.2 0 2.6 2 3.2 5H8.8C9.4 5 10.8 3 12 3zM3.3 10h4.9a20 20 0 0 0 0 4H3.3a9 9 0 0 1 0-4zm.8 6h4.3c.3 1.7.8 3.1 1.5 4.3A9 9 0 0 1 4.1 16zm4.3-8H4.1a9 9 0 0 1 5.8-4.3C9.2 4.9 8.7 6.3 8.4 8zM12 21c-1.2 0-2.6-2-3.2-5h6.4c-.6 3-2 5-3.2 5zm3.4-7H8.6a18 18 0 0 1 0-4h6.8a18 18 0 0 1 0 4zm-1.3 6.3c.7-1.2 1.2-2.6 1.5-4.3h4.3a9 9 0 0 1-5.8 4.3zM15.8 14a20 20 0 0 0 0-4h4.9a9 9 0 0 1 0 4zm-.2-6c-.3-1.7-.8-3.1-1.5-4.3A9 9 0 0 1 19.9 8z"/></svg>
        <span>VEGAAVIATION.COM</span>
      </div>
      <div class="contact-item contact-phone">
        <svg viewBox="0 0 24 24" aria-hidden="true"><path d="M6.6 10.8a15 15 0 0 0 6.6 6.6l2.2-2.2c.3-.3.7-.4 1-.2 1.1.4 2.3.6 3.6.6.6 0 1 .4 1 1V20c0 .6-.4 1-1 1A17 17 0 0 1 3 4c0-.6.4-1 1-1h3.5c.6 0 1 .4 1 1 0 1.3.2 2.5.6 3.6.1.3 0 .7-.2 1z"/></svg>
        <span>900-555-0142</span>
      </div>
      <div class="contact-item contact-mail">
        <svg viewBox="0 0 24 24" aria-hidden="true"><path d="M2 9l10 7 10-7v12H2zM2 8l4-3V2h12v3l4 3-10 7zM8 5h8v1.5H8zm0 3h8v1.5H8z"/></svg>
        <span>INFO@VEGAAVIATION.COM</span>
      </div>
    </footer>
  </section>
</body>
</html>
```